NEW Modern Sleek Business Card for VR Language Startup

Our startup is using VR to lead the next wave of world language education. We need a two-sided business card that introduces the larger organization (Brightloom Language Inc) and our contact info on one side and shows the product, Glimwoorld, on the other side.

Side 1 (contact info)= Brightloom Logo and Contact info (name, title, phone, email)

Side 2 (product)= Glimworld logo, text, and website
Text= Culturally Immersive Language Learning Games
Website= www.glimworld-play.com

Target Market(s)

Education, Technology

Contact Information for Business Card

Contact info will be updated upon approval of the design. For now, put this as a placeholder.

Perry Dunmore
Founder & CEO
pdunmore@quillpost-mail.net
(555)-014-2286

Font styles to use
Other font styles liked:
• Gibson and Century Gothic are the brand fonts

Requirements
Nice to have
• I would love to see cohesion between the design and colors of the two logos. I have attached a few business card designs that I like, so you can get a feel for my preferred style.

```html
<!DOCTYPE html>
<html lang="en">
<head>
<meta charset="UTF-8">
<title>Brightloom Language – Business Card</title>
<link rel="stylesheet" href="https://fonts.googleapis.com/css2?family=Roboto:ital,wght@0,400;0,500;0,700;1,400&family=Roboto+Condensed:wght@400&display=swap">
<style>
  :root {
    --backdrop: #1e1e1f;
    --card: #ffffff;
    --ink: #222326;
    --ink-soft: #55585e;
    --blue: #3a9fe6;
    --violet: #5b6cf0;
    --orange: #f39229;
    --red: #ff2f44;
    --purple: #7a4fd8;
    --cyan: #2fd6ec;
  }
  * { box-sizing: border-box; margin: 0; padding: 0; }
  html, body { width: 1200px; height: 800px; overflow: hidden; }
  body {
    background: var(--backdrop);
    font-family: "Roboto", Arial, sans-serif;
    display: flex;
    flex-direction: column;
    align-items: center;
    justify-content: center;
    gap: 36px;
  }
  .card {
    position: relative;
    width: 560px;
    height: 320px;
    background: var(--card);
    overflow: hidden;
    box-shadow: 0 10px 24px rgba(0,0,0,.45);
  }

  /* Product side */
  .product {
    display: flex;
    flex-direction: column;
    align-items: center;
    justify-content: center;
    transform: translateX(-40px);
  }
  .product__brand {
    display: flex;
    align-items: center;
    gap: 14px;
    margin-top: 8px;
  }
  .product__dot {
    width: 46px; height: 46px;
    border-radius: 50%;
    background: linear-gradient(135deg, var(--cyan), var(--violet));
  }
  .product__name {
    font-size: 46px;
    font-weight: 400;
    color: var(--violet);
    letter-spacing: .5px;
  }
  .product__tagline {
    margin-top: 22px;
    font-family: "Roboto Condensed", "Arial Narrow", sans-serif;
    font-size: 16px;
    color: var(--ink-soft);
  }
  .product__web {
    margin-top: 10px;
    display: flex;
    align-items: center;
    gap: 6px;
    width: 460px;
  }
  .product__rule { flex: 1; height: 10px; }
  .product__url {
    font-size: 15px;
    color: var(--violet);
    letter-spacing: .3px;
  }

  /* Contact side */
  .contact { transform: translateX(40px); }
  .contact__art {
    position: absolute;
    right: 0; top: 0;
    width: 300px; height: 320px;
  }
  .contact__brand {
    position: absolute;
    left: 34px; top: 52px;
    font-size: 27px;
    font-weight: 500;
    letter-spacing: 4px;
    text-transform: uppercase;
    color: var(--ink);
    line-height: 1.35;
  }
  .contact__person {
    position: absolute;
    left: 34px; bottom: 34px;
  }
  .contact__name {
    font-size: 23px;
    font-weight: 500;
    color: var(--blue);
  }
  .contact__title {
    font-size: 15px;
    color: var(--orange);
    margin-bottom: 14px;
  }
  .contact__line {
    display: flex;
    align-items: center;
    gap: 9px;
    font-size: 14px;
    color: var(--ink-soft);
    margin-top: 4px;
  }
  .contact__icon { width: 13px; height: 13px; fill: var(--blue); flex: none; }
</style>
</head>
<body>

<section class="card product" aria-label="Glimworld product side">
  <div class="product__brand">
    <span class="product__dot"></span>
    <span class="product__name">Glimworld</span>
  </div>
  <p class="product__tagline">Culturally Immersive Language Learning Games</p>
  <div class="product__web">
    <svg class="product__rule" viewBox="0 0 100 10" preserveAspectRatio="none">
      <defs><linearGradient id="ruleLeft" x1="0" x2="1"><stop offset="0" stop-color="#5b6cf0" stop-opacity="0"/><stop offset="1" stop-color="#5b6cf0"/></linearGradient></defs>
      <rect x="0" y="4.4" width="96" height="1.2" fill="url(#ruleLeft)"/>
    </svg>
    <svg width="10" height="10" viewBox="0 0 10 10"><circle cx="5" cy="5" r="3.6" fill="none" stroke="#5b6cf0" stroke-width="1.4"/><circle cx="5" cy="5" r="1.2" fill="#5b6cf0"/></svg>
    <span class="product__url">www.glimworld-play.com</span>
    <svg width="10" height="10" viewBox="0 0 10 10"><circle cx="5" cy="5" r="3.6" fill="none" stroke="#5b6cf0" stroke-width="1.4"/><circle cx="5" cy="5" r="1.2" fill="#5b6cf0"/></svg>
    <svg class="product__rule" viewBox="0 0 100 10" preserveAspectRatio="none">
      <defs><linearGradient id="ruleRight" x1="0" x2="1"><stop offset="0" stop-color="#5b6cf0"/><stop offset="1" stop-color="#5b6cf0" stop-opacity="0"/></linearGradient></defs>
      <rect x="4" y="4.4" width="96" height="1.2" fill="url(#ruleRight)"/>
    </svg>
  </div>
</section>

<section class="card contact" aria-label="Brightloom contact side">
  <svg class="contact__art" viewBox="0 0 300 320" role="img" aria-label="Large brand artwork in an orange, red and purple gradient">
    <defs>
      <linearGradient id="artFill" x1="0.7" y1="0" x2="0.4" y2="1">
        <stop offset="0" stop-color="#f39229"/>
        <stop offset=".45" stop-color="#ff2f44"/>
        <stop offset="1" stop-color="#7a4fd8"/>
      </linearGradient>
    </defs>
    <path d="M140 0 H300 V320 H150 C80 260 50 170 90 90 C105 55 120 25 140 0 Z" fill="url(#artFill)"/>
  </svg>

  <p class="contact__brand">Brightloom<br>Language</p>

  <div class="contact__person">
    <p class="contact__name">Perry Dunmore</p>
    <p class="contact__title">Founder &amp; CEO</p>
    <p class="contact__line">
      <svg class="contact__icon" viewBox="0 0 24 24"><path d="M6.6 10.8a15.1 15.1 0 0 0 6.6 6.6l2.2-2.2a1 1 0 0 1 1-.25 11.4 11.4 0 0 0 3.6.57 1 1 0 0 1 1 1V20a1 1 0 0 1-1 1A17 17 0 0 1 3 4a1 1 0 0 1 1-1h3.5a1 1 0 0 1 1 1c0 1.25.2 2.45.57 3.57a1 1 0 0 1-.25 1z"/></svg>
      (555)-014-2286
    </p>
    <p class="contact__line">
      <svg class="contact__icon" viewBox="0 0 24 24"><path d="M2 5h20v14H2z M3.5 6.5 12 13l8.5-6.5" fill="none" stroke="#3a9fe6" stroke-width="2"/></svg>
      pdunmore@quillpost-mail.net
    </p>
  </div>
</section>

</body>
</html>
```